We are a local Communty Pharmacy wishing to promote and market a specialised Pharmaceutical Service

We would like a design that is professional and enticing ( according to the brief In attached files)
We wish to Market Compounding Pharmacy as a specialist side of our business.
We have the expertise a purpose built preparation laboratory.
The main purpose is an Internet presence that entices prospective patients to contact or visit our physical store.

Target Market(s)

Patients Medicos and Veterinary clients

Industry/Entity Type

Pharmacy

Coding

Coded - Design and coding required

Number of Pages Required

1 page

Requirements
Must have
• Clear friendly image
Nice to have
• soft enticing feel
Should not have
• No crass loud unprofessional elements

```html
<!DOCTYPE html>
<html lang="en">
<head>
<meta charset="utf-8">
<title>Westbrook Pharmacy – Compounding Pharmacy</title>
<link href="https://fonts.googleapis.com/css2?family=Open+Sans:wght@400;600;700&family=Oswald:wght@400;500&display=swap" rel="stylesheet">
<style>
:root{
  --blue:#1c8fd6;
  --blue-dark:#0e6fb0;
  --blue-soft:#cfe9f8;
  --band:#e9f0f5;
  --ink:#3a3f45;
  --muted:#7c858e;
  --footer:#1e2124;
  --footer-line:#2d3135;
  --white:#ffffff;
}
*{margin:0;padding:0;box-sizing:border-box}
html,body{width:700px;height:1200px;overflow:hidden;background:var(--white);font-family:"Open Sans",Arial,sans-serif;color:var(--ink)}
.page{width:700px;height:1200px;position:relative}

/* header */
.site-header{height:65px;display:flex;align-items:center;justify-content:space-between;padding:0 34px 0 30px}
.brand{display:flex;align-items:center;gap:8px}
.brand-mark{width:22px;height:22px;background:var(--blue);border-radius:4px}
.brand-name{font-size:17px;font-weight:700;color:var(--blue-dark);letter-spacing:.5px}
.header-contact{display:flex;gap:14px;font-size:7.5px;line-height:1.4;color:var(--muted)}
.header-contact .addr{width:170px;display:flex;gap:5px}
.header-contact .phones{display:flex;flex-direction:column;gap:4px}
.ic{flex:none}

/* nav */
.main-nav{height:38px;background:var(--blue);display:flex;align-items:center;padding:0 30px}
.main-nav a{color:var(--white);text-decoration:none;font-size:8px;font-weight:700;padding:0 20px;height:38px;line-height:38px;text-transform:uppercase}
.main-nav a.active{background:var(--blue-dark)}
.search{margin-left:auto;width:130px;height:20px;border:1px solid rgba(255,255,255,.7);border-radius:2px;display:flex;align-items:center;justify-content:space-between;padding:0 7px;color:#e8f4fc;font-size:7.5px}

/* hero */
.hero{position:relative;height:375px;overflow:hidden}
.hero-photo{position:absolute;inset:0;background:linear-gradient(90deg,#d7e3ea 0%,#eef3f6 35%,#f6f8f9 55%,#d9e4eb 100%)}
.hero-arrow{position:absolute;top:175px;width:28px;height:28px;border-radius:50%;background:rgba(80,90,100,.45);display:flex;align-items:center;justify-content:center}
.hero-arrow.prev{left:22px}.hero-arrow.next{right:22px}
.hero-title{position:absolute;left:0;right:0;top:258px;text-align:center;font-family:Oswald,sans-serif;font-size:44px;font-weight:500;color:var(--blue);letter-spacing:1px;text-shadow:0 1px 2px rgba(255,255,255,.7)}
.hero-sub{position:absolute;left:0;right:0;top:318px;text-align:center}
.hero-sub span{display:inline-block;background:var(--blue);color:var(--white);font-size:9px;font-weight:600;letter-spacing:1px;padding:6px 40px}

/* about */
.about{padding:20px 45px 0;text-align:center;background:#f4f6f8;height:292px}
.section-title{font-family:Oswald,sans-serif;font-size:21px;font-weight:500;color:var(--ink);letter-spacing:.5px}
.rule{width:40px;height:2px;background:var(--blue);margin:6px auto 14px}
.about p{font-size:7.2px;line-height:1.65;color:var(--muted);text-align:left;margin-bottom:9px}
.btn{display:inline-block;margin-top:14px;background:var(--blue-dark);color:var(--white);font-size:8px;font-weight:700;padding:7px 14px;border-radius:2px}

/* features */
.features{background:var(--band);height:235px;padding-top:28px;text-align:center}
.cards{display:flex;justify-content:center;gap:22px;margin-top:6px}
.card{width:190px;height:150px;background:var(--white);box-shadow:0 1px 3px rgba(0,0,0,.08)}
.card-top{height:82px;background:var(--blue-soft);display:flex;flex-direction:column;align-items:center;justify-content:center;gap:6px}
.card-top.highlight{background:var(--blue)}
.card-icon{width:30px;height:30px;border-radius:50%;background:var(--white);display:flex;align-items:center;justify-content:center}
.card-title{font-size:9.5px;font-weight:700;color:var(--blue-dark);text-transform:uppercase}
.card-top.highlight .card-title{color:var(--white)}
.card p{font-size:6.8px;line-height:1.6;color:var(--muted);padding:10px 14px 0}

/* footer */
.site-footer{background:var(--footer);height:173px;padding:24px 45px 0;display:flex;justify-content:space-between;color:#c9ced3}
.footer-title{font-size:11px;font-weight:700;color:var(--white);text-transform:uppercase}
.footer-title em{font-style:normal;color:var(--blue)}
.hours{font-size:7px;margin-top:10px;line-height:1.8}
.days{display:flex;gap:8px;font-size:6.8px}
.days b{color:var(--blue)}
.socials{display:flex;gap:8px;margin-top:20px}
.socials span{width:18px;height:18px;border-radius:50%;border:1px solid var(--blue)}
.contact{width:210px;font-size:7px;line-height:1.7}
.contact .row{display:flex;gap:6px;margin-top:6px;align-items:flex-start}
.copyright{position:absolute;left:0;right:0;bottom:0;height:22px;background:#161819;border-top:1px solid var(--footer-line);color:#7d848a;font-size:6.5px;display:flex;align-items:center;justify-content:space-between;padding:0 45px}
</style>
</head>
<body>
<div class="page">

  <header class="site-header">
    <div class="brand">
      <span class="brand-mark"></span>
      <span class="brand-name">WESTBROOK</span>
    </div>
    <div class="header-contact">
      <div class="addr">
        <svg class="ic" width="8" height="10" viewBox="0 0 8 10"><path d="M4 0a4 4 0 0 0-4 4c0 3 4 6 4 6s4-3 4-6a4 4 0 0 0-4-4z" fill="#1c8fd6"/><circle cx="4" cy="4" r="1.4" fill="#fff"/></svg>
        <span>WESTBROOK COMMUNITY PHARMACY (UNIT 4) HARLOW ROAD WESTBROOK, WESTERN AUSTRALIA</span>
      </div>
      <div class="phones">
        <span>&#9742; 08 9000 4410</span>
        <span>&#9993; care@westbrookpharmacy.example</span>
      </div>
      <div class="phones">
        <span>&#9742; 08 9000 4411</span>
      </div>
    </div>
  </header>

  <nav class="main-nav">
    <a class="active">Home</a><a>About Us</a><a>Products</a><a>Event</a><a>Contact Us</a>
    <div class="search"><span>Search</span>
      <svg width="8" height="8" viewBox="0 0 8 8"><circle cx="3.3" cy="3.3" r="2.5" fill="none" stroke="#fff" stroke-width="1"/><path d="M5.2 5.2 7.6 7.6" stroke="#fff" stroke-width="1"/></svg>
    </div>
  </nav>

  <section class="hero">
    <div class="hero-photo" role="img" aria-label="Smiling pharmacist in a white coat in front of pharmacy shelves stocked with medicines"></div>
    <div class="hero-arrow prev"><svg width="8" height="10" viewBox="0 0 8 10"><path d="M6 1 2 5l4 4" fill="none" stroke="#fff" stroke-width="1.6"/></svg></div>
    <div class="hero-arrow next"><svg width="8" height="10" viewBox="0 0 8 10"><path d="M2 1l4 4-4 4" fill="none" stroke="#fff" stroke-width="1.6"/></svg></div>
    <h1 class="hero-title">COMPOUNDING PHARMACY</h1>
    <div class="hero-sub"><span>IS CUSTOMIZED MEDICATIONS FOR PATIENTS</span></div>
  </section>

  <section class="about">
    <h2 class="section-title">WHAT IS COMPOUNDING PHARMACY?</h2>
    <div class="rule"></div>
    <p>Many people have heard of compounding but are not sure what it means. Compounding is the preparation of a medicine made to suit one patient. Our pharmacists work from a prescription to mix ingredients in the exact strength, dose and form that a person needs. It is one of the oldest parts of pharmacy and remains a vital service for patients, doctors and vets today.</p>
    <p>Our team has the training and equipment to prepare medicines in a purpose built laboratory. We can remove allergens such as lactose or dyes, change a tablet into a liquid, cream or lozenge, and add flavours that make treatment easier for children and pets. Each preparation is checked with care before it leaves our store.</p>
    <p>We work closely with prescribers to find the right option for each patient. If you would like to know more, speak with our pharmacists in store or contact us to discuss how compounding could help you.</p>
    <span class="btn">READ MORE</span>
  </section>

  <section class="features">
    <h2 class="section-title">FEATURE ITEMS</h2>
    <div class="rule"></div>
    <div class="cards">
      <div class="card">
        <div class="card-top">
          <div class="card-icon"><svg width="14" height="14" viewBox="0 0 14 14"><rect x="3" y="1" width="8" height="12" rx="1" fill="none" stroke="#1c8fd6" stroke-width="1.3"/><path d="M5 5h4M5 8h4" stroke="#1c8fd6" stroke-width="1.2"/></svg></div>
          <div class="card-title">HRT Article</div>
        </div>
        <p>Learn how tailored hormone therapy can be prepared to suit your needs and dose.</p>
      </div>
      <div class="card">
        <div class="card-top highlight">
          <div class="card-icon"><svg width="14" height="14" viewBox="0 0 14 14"><path d="M7 2v10M2 7h10" stroke="#1c8fd6" stroke-width="2"/></svg></div>
          <div class="card-title">Scar Therapy</div>
        </div>
        <p>Custom creams and gels made to help soften and improve the look of scars.</p>
      </div>
      <div class="card">
        <div class="card-top">
          <div class="card-icon"><svg width="14" height="14" viewBox="0 0 14 14"><rect x="2" y="5" width="10" height="4" rx="2" fill="none" stroke="#1c8fd6" stroke-width="1.3"/><path d="M7 5v4" stroke="#1c8fd6" stroke-width="1.3"/></svg></div>
          <div class="card-title">Thyroid Extract</div>
        </div>
        <p>Thyroid preparations compounded to the exact strength your doctor prescribes.</p>
      </div>
    </div>
  </section>

  <footer class="site-footer">
    <div>
      <div class="footer-title">Opening <em>Hours</em></div>
      <div class="hours">7 DAYS A WEEK
        <div class="days"><span><b>M</b> 8-7</span><span><b>T</b> 8-7</span><span><b>W</b> 8-7</span><span><b>T</b> 8-7</span><span><b>F</b> 8-7</span><span><b>S</b> 9-5</span><span><b>S</b> 9-5</span></div>
      </div>
      <div class="socials"><span></span><span></span><span></span><span></span><span></span></div>
    </div>
    <div class="contact">
      <div class="footer-title">Contact <em>Info</em></div>
      <div class="row" style="margin-top:10px">
        <svg class="ic" width="7" height="9" viewBox="0 0 8 10"><path d="M4 0a4 4 0 0 0-4 4c0 3 4 6 4 6s4-3 4-6a4 4 0 0 0-4-4z" fill="#1c8fd6"/></svg>
        <span>WESTBROOK COMMUNITY PHARMACY (UNIT 4) HARLOW ROAD WESTBROOK, WESTERN AUSTRALIA</span>
      </div>
      <div class="row"><span>&#9742; 08 9000 4410</span><span>&#9742; 08 9000 4411</span></div>
      <div class="row"><span>&#9993; care@westbrookpharmacy.example</span></div>
    </div>
    <div class="copyright"><span>Copyright © 2016 Westbrook Pharmacy. All rights reserved.</span><span>1 · 2</span></div>
  </footer>

</div>
</body>
</html>
```